Ward Compass Business Card Design*

We need a business card design for our company Ward Compass. Our company is specialized in providing online consulting services regarding medical institutions, hospitals and doctors. We work with patients worldwide looking to choose between healthcare providers. We have a website you may use as a reference, where we list doctors and clinics worldwide. So we target Medical providers as well as patients worldwide.
Target Market(s)
Medical Providers and patients around the world
Industry/Entity Type
Medical
Contact Information for Business Card
Salwa Kettani
CEO
+90 612 348 2175
info@wardcompass.example
www.wardcompass.example
14 Annakhil 7 H.R.B. Rabat, Morocco
Requirements
Must have
- Company logo/name on one full side, personal info and smaller logo and company name on the other side.
Nice to have
- Smart and elegant design

```html
<!DOCTYPE html>
<html lang="en">
<head>
<meta charset="UTF-8">
<title>Ward Compass — Business Card</title>
<link href="https://fonts.googleapis.com/css2?family=Montserrat:wght@500;700&family=Open+Sans:wght@400&display=swap" rel="stylesheet">
<style>
  :root {
    --navy: #15386a;
    --white: #ffffff;
    --grey: #7d7d7d;
    --backdrop: #e9ebef;
  }
  html, body {
    margin: 0;
    width: 1200px;
    height: 1000px;
    overflow: hidden;
    background: var(--backdrop);
  }
  .canvas {
    position: relative;
    width: 1200px;
    height: 1000px;
  }
  .card {
    position: absolute;
    width: 760px;
    height: 434px;
    border-radius: 22px;
    overflow: hidden;
    box-shadow: 0 10px 28px rgba(20, 30, 50, 0.25);
  }
  .card--back {
    left: 340px;
    top: 44px;
    background: var(--navy);
    display: flex;
    align-items: center;
    justify-content: center;
    gap: 16px;
  }
  .card--front {
    left: 100px;
    top: 518px;
    background: var(--white);
  }
  .brand-dot {
    width: 18px;
    height: 18px;
    border-radius: 50%;
    background: var(--white);
  }
  .brand-name {
    font-family: "Montserrat", sans-serif;
    font-weight: 700;
    font-size: 40px;
    letter-spacing: 2px;
    text-transform: uppercase;
    color: var(--white);
  }
  .front-panel {
    position: absolute;
    inset: 0;
  }
  .holder {
    position: absolute;
    left: 50px;
    top: 54px;
    color: var(--white);
    font-family: "Montserrat", sans-serif;
    font-weight: 700;
  }
  .holder-name {
    margin: 0;
    font-size: 26px;
    letter-spacing: 0.5px;
    text-transform: uppercase;
  }
  .holder-role {
    margin: 4px 0 0;
    font-size: 22px;
  }
  .contact {
    position: absolute;
    left: 50px;
    top: 228px;
    color: var(--white);
    font-family: "Open Sans", sans-serif;
    font-size: 17px;
    line-height: 1.35;
  }
  .contact-address {
    margin: 0 0 14px;
  }
  .contact-list {
    list-style: none;
    margin: 0;
    padding: 0;
  }
  .contact-list li {
    display: flex;
    align-items: center;
    gap: 10px;
    margin-bottom: 6px;
  }
  .contact-icon {
    width: 16px;
    height: 16px;
    flex: none;
  }
  .front-brand {
    position: absolute;
    left: 470px;
    top: 0;
    width: 270px;
    height: 434px;
    display: flex;
    flex-direction: column;
    align-items: center;
    justify-content: center;
    gap: 18px;
  }
  .front-brand-dot {
    width: 26px;
    height: 26px;
    border-radius: 50%;
    background: var(--navy);
  }
  .front-brand-name {
    font-family: "Montserrat", sans-serif;
    font-weight: 700;
    font-size: 36px;
    line-height: 1.15;
    letter-spacing: 2px;
    text-transform: uppercase;
    text-align: center;
    color: var(--navy);
  }
</style>
</head>
<body>
<main class="canvas">

  <section class="card card--back" aria-label="Card back">
    <span class="brand-dot"></span>
    <span class="brand-name">Ward Compass</span>
  </section>

  <section class="card card--front" aria-label="Card front">
    <svg class="front-panel" width="760" height="434" viewBox="0 0 760 434" aria-hidden="true">
      <path d="M0 0 H480 C370 60 340 180 368 290 C392 372 440 412 510 434 H0 Z" fill="var(--navy)"/>
    </svg>

    <div class="holder">
      <p class="holder-name">Salwa Kettani</p>
      <p class="holder-role">CEO</p>
    </div>

    <div class="contact">
      <p class="contact-address">14 Annakhil 7 H.R.B.<br>Rabat, Morocco</p>
      <ul class="contact-list">
        <li>
          <svg class="contact-icon" viewBox="0 0 16 16" aria-hidden="true">
            <path d="M4 1.5 L6.2 4.2 5 5.8 C5.8 7.8 8.2 10.2 10.2 11 L11.8 9.8 14.5 12 13 14.3 C8 14.5 1.5 8 1.7 3 Z" fill="var(--white)"/>
          </svg>
          +90 612 348 2175
        </li>
        <li>
          <svg class="contact-icon" viewBox="0 0 16 16" aria-hidden="true">
            <rect x="1" y="3" width="14" height="10" rx="1" fill="none" stroke="var(--white)" stroke-width="1.6"/>
            <path d="M1.5 3.5 L8 9 14.5 3.5" fill="none" stroke="var(--white)" stroke-width="1.6"/>
          </svg>
          info@wardcompass.example
        </li>
        <li>
          <svg class="contact-icon" viewBox="0 0 16 16" aria-hidden="true">
            <circle cx="8" cy="8" r="6.5" fill="none" stroke="var(--white)" stroke-width="1.5"/>
            <ellipse cx="8" cy="8" rx="2.8" ry="6.5" fill="none" stroke="var(--white)" stroke-width="1.2"/>
            <path d="M1.5 8 H14.5" stroke="var(--white)" stroke-width="1.2"/>
          </svg>
          www.wardcompass.example
        </li>
      </ul>
    </div>

    <div class="front-brand">
      <span class="front-brand-dot"></span>
      <span class="front-brand-name">Ward<br>Compass</span>
    </div>
  </section>

</main>
</body>
</html>
```